BrivoTerna. Lantern of the Steady Harvest. Business card

Professional business card for BrivoTerna (Lantern of the Steady Harvest)
My rationale: Strategy-> Execution-> Results-> Value that lead to the BrivoTerna name: We put the Lantern of the Steady Harvest.
We deliver value to our customers helping them at defining a good strategy (cyan arrow). 90% of well formulated strategies fail due to poor execution so we also consider strategical execution very important (green arrow). Due to the execution we obtain the results (blue arrow). Finally, the results provide feedback to redefine strategy, and the new strategy has to be executed and new results obtained providing new feedback and on and on. It's like a wheel that finally, must create corporate value: value for shareholders, staholders, employees, providers...-

Target Market(s)

CEOs and steering comitees , invewrnent funds

Industry/Entity Type

Business Consultant

Contact Information for Business Card

Teodoro Vinsquel
CEO & Founder
teodoro.vinsquel@brivoterna-example.com
Mobile: +34 655.803.912
www.brivoterna-example.com

Colors

Designer to choose colors to be used in the design.

Requirements
Nice to have
• Nice to hace the words: Strategy, execution, results
• Nice to vave the claim: Lantern of the Steady Harvest
• The three colors should be shown:
• cyan for STRATEGY
• green for EXECUTION
• blue for RESULTS
Should not have
• Complete black background

```html
<!DOCTYPE html>
<html lang="en">
<head>
<meta charset="utf-8">
<title>BrivoTerna — Business Card</title>
<link rel="stylesheet" href="https://fonts.googleapis.com/css2?family=Open+Sans:wght@400;600;700;800&display=swap">
<style>
  :root {
    --navy: #0a3a9c;
    --cyan: #1ba9e6;
    --green: #8cc63f;
    --ink: #3a3f47;
    --paper: #ffffff;
    --backdrop: #e6e9ee;
  }
  * { box-sizing: border-box; margin: 0; padding: 0; }
  html, body {
    width: 1200px; height: 900px; overflow: hidden;
    background: var(--backdrop);
    font-family: "Open Sans", Arial, sans-serif;
  }
  .canvas { position: relative; width: 1200px; height: 900px; }
  .card {
    position: absolute; width: 620px; height: 354px;
    background: var(--paper); border-radius: 18px; overflow: hidden;
    box-shadow: 0 10px 30px rgba(20, 30, 60, .18);
  }
  .card--front { left: 70px; top: 70px; }
  .card--back { left: 510px; top: 476px; }
  .card__band { position: absolute; inset: 0; }

  .holder { position: absolute; right: 30px; top: 18px; text-align: right; color: #fff; }
  .holder__name { font-size: 22px; font-weight: 700; letter-spacing: .2px; }
  .holder__role { font-size: 13px; font-weight: 400; margin-top: 1px; }

  .process-graphic {
    position: absolute; right: 28px; top: 138px; width: 200px; height: 140px;
    border-radius: 10px;
    background: linear-gradient(160deg, rgba(10,58,156,.22) 0%, rgba(140,198,63,.22) 50%, rgba(27,169,230,.22) 100%);
  }

  .brand-name {
    position: absolute; left: 36px; top: 150px;
    font-size: 44px; font-weight: 800; color: var(--navy); letter-spacing: -1px;
  }

  .contacts { position: absolute; left: 38px; top: 258px; list-style: none; }
  .contacts li { display: flex; align-items: center; gap: 10px; font-size: 14px; color: var(--ink); line-height: 25px; }
  .contacts svg { width: 16px; height: 16px; flex: none; }

  .back-brand {
    position: absolute; left: 0; right: 0; top: 112px; text-align: center;
    font-size: 78px; font-weight: 800; color: var(--navy); letter-spacing: -2px;
  }
  .tagline {
    position: absolute; left: 60px; right: 60px; top: 232px;
    display: flex; align-items: center; gap: 14px;
    font-size: 17px; color: var(--navy); white-space: nowrap;
  }
  .tagline::before, .tagline::after { content: ""; flex: 1; height: 1px; background: var(--cyan); }
</style>
</head>
<body>
<div class="canvas">

  <section class="card card--front">
    <svg class="card__band" viewBox="0 0 620 354" aria-hidden="true">
      <path d="M0 0 H620 V108 Q330 58 0 44 Z" fill="var(--navy)"/>
      <path d="M0 44 Q330 58 620 108 V122 Q330 74 0 58 Z" fill="var(--cyan)"/>
      <path d="M0 58 Q170 64 320 86 Q160 72 0 84 Z" fill="var(--green)"/>
    </svg>

    <div class="holder">
      <div class="holder__name">Teodoro Vinsquel</div>
      <div class="holder__role">CEO &amp; Founder</div>
    </div>

    <div class="process-graphic" role="img" aria-label="Process graphic: strategy in cyan, execution in green and results in navy, rising as arrows"></div>

    <div class="brand-name">BrivoTerna</div>

    <ul class="contacts">
      <li>
        <svg viewBox="0 0 16 16"><circle cx="8" cy="8" r="8" fill="var(--navy)"/><path d="M5.5 4.5 L7 4.2 L7.6 6.2 L6.7 7 Q7.4 8.7 9 9.3 L9.8 8.4 L11.8 9 L11.5 10.6 Q8 11 5.5 8 Q4.8 6 5.5 4.5Z" fill="#fff"/></svg>
        +34 655.803.912
      </li>
      <li>
        <svg viewBox="0 0 16 16"><circle cx="8" cy="8" r="8" fill="var(--navy)"/><rect x="4" y="5" width="8" height="6" rx="1" fill="#fff"/><path d="M4 5.5 L8 8.5 L12 5.5" stroke="var(--navy)" stroke-width="1" fill="none"/></svg>
        teodoro.vinsquel@brivoterna-example.com
      </li>
      <li>
        <svg viewBox="0 0 16 16"><circle cx="8" cy="8" r="8" fill="var(--navy)"/><circle cx="8" cy="8" r="4" stroke="#fff" stroke-width="1" fill="none"/><path d="M4 8 H12 M8 4 Q5.5 8 8 12 M8 4 Q10.5 8 8 12" stroke="#fff" stroke-width="1" fill="none"/></svg>
        www.brivoterna-example.com
      </li>
    </ul>
  </section>

  <section class="card card--back">
    <div class="back-brand">BrivoTerna</div>
    <div class="tagline">Lantern of the Steady Harvest</div>
  </section>

</div>
</body>
</html>
```